Brand Identity & Marketing Website Design for Professional Football Scouting Software

Merivantalo is a professional football scouting report generation software.
It is a standalone desktop application that allows football clubs, agencies and players to generate structured, executive-level A4 PDF scouting reports.
This is NOT:
a betting platform
a fan website
a football news blog
a SaaS subscription platform
This is a premium document-generation software tool designed for professional use inside football organizations.
The brand must reflect:
• Structure
• Authority
• Precision
• Professionalism
• Trust
• Executive-level quality
Think consulting firm, performance analysis tool, structured business software.
Not flashy sports media.
What We Need
We are looking for:
1️⃣ Logo Design
2️⃣ Full Brand Identity System
3️⃣ Marketing Website UI/UX Design
(Development is NOT included in this job.)
Important Product Context
Merivantalo is sold as a one-time purchase software package.
After purchase: • Customers download the software
• Install it locally
• Generate reports offline
There is no recurring subscription.
There is no SaaS login platform.
The website is a marketing and purchase website only.
1️⃣ Logo Design
The logo must:
• Be professional and timeless
• Work in both light and dark backgrounds
• Be scalable (website header, app icon, favicon)
• Avoid cliché football logo styles (no shields, mascots, flashy emblems)
• Feel modern, clean, and strong
We prefer:
• Clean typography-based logo
• OSTRAL symbol integration
• Strong visual balance
• Suitable for software branding
Name:
Merivantalo
Optional tagline:
The leading platform for professional football scouting reports
Deliver:
• Full logo
• Icon-only version (for desktop app icon)
• Light & dark variations
2️⃣ Brand Identity System
We need a structured design system that supports:
• Marketing website
• Desktop application UI
• PDF report previews
Please define:
• Primary color palette
• Secondary color palette
• Accent colors
• Typography system (professional, highly readable)
• Heading hierarchy
• UI styling guidelines
• Light mode & dark mode principles
The design must feel:
• OSTRAL
• Grid-based
• Clean
• Premium
• Corporate
Avoid:
• Neon colors
• Heavy gradients
• Overly sporty visuals
• Gaming aesthetics
3️⃣ Marketing Website Design (UI/UX Only)
We need full website design in Figma for:
• Homepage
• Product Overview
• Packages Page (Club / Agency / Player)
• How It Works
• Demo Section
• FAQ
• Contact
• Purchase / Download Page
Design must include:
• Hero section
• Feature explanation sections
• Structured benefits
• Product screenshots placement
• Pricing comparison layout
• Clear call-to-action areas
• Professional footer
Responsive design required (Desktop-first, mobile adaptation).
Important:
Content copy will be provided by us.
Designer focuses on layout, structure, hierarchy and visual design.
Target Audience
• Professional football clubs
• Scouting departments
• Player agencies
• Semi-professional and professional players
This is primarily B2B, with some B2C.
Style Direction
We are looking for:
• Strong typography
• Balanced whitespace
• Structured layouts
• Subtle but confident use of color
• Professional photography (if used)
• Premium software feel
The website and brand must feel trustworthy and high-level.
Deliverables
• Logo files (AI, SVG, PNG)
• Brand guideline document (PDF)
• Figma file with full website UI
• Icon assets (app icon, favicon)
• Color and typography system

Need extra days to review

```html
<!DOCTYPE html>
<html lang="en">
<head>
<meta charset="utf-8">
<title>Merivantalo — Professional Football Scouting Reports</title>
<link href="https://fonts.googleapis.com/css2?family=Montserrat:wght@400;500;600;700;800&display=swap" rel="stylesheet">
<style>
:root{
  --navy:#14244a;
  --navy-2:#1c2e5c;
  --blue:#1a56c6;
  --blue-2:#2a6ae0;
  --sky:#e4edfa;
  --sky-2:#f1f5fc;
  --ink:#1b2230;
  --muted:#6b7385;
  --line:#dfe5ef;
  --green:#22a45d;
  --amber:#e8a21b;
  --dark-ui:#171b26;
  --white:#ffffff;
}
*{margin:0;padding:0;box-sizing:border-box}
html,body{width:1200px;height:3971px;overflow:hidden}
body{font-family:'Montserrat',sans-serif;color:var(--ink);background:var(--white)}
.page{position:relative;width:1200px;height:3971px;overflow:hidden}
.abs{position:absolute}
.center-text{position:absolute;left:0;width:1200px;text-align:center}
.btn{position:absolute;display:flex;align-items:center;justify-content:space-between;gap:10px;padding:0 6px 0 12px;font-weight:600;font-size:15px;color:#fff;background:var(--blue);border-radius:2px}
.btn .chev{width:26px;height:26px;background:#fff;border-radius:2px;display:flex;align-items:center;justify-content:center}
.btn.dark{background:var(--navy)}
.btn.light{background:#fff;color:var(--navy)}
.btn.light .chev{background:var(--navy)}

/* backgrounds */
.hero-bg{left:0;top:0;width:1200px;height:900px;background:linear-gradient(180deg,#dbe6f7 0%,#e8effa 100%)}
.band-bg{left:0;top:2560px;width:1200px;height:260px;background:linear-gradient(180deg,#fff 0%,#dfe8f7 100%)}
.foot-bg{left:0;top:3200px;width:1200px;height:771px;background:linear-gradient(180deg,#fff 0%,#e8eef9 100%)}

/* top bar */
.topbar{left:0;top:0;width:1200px;height:42px;background:var(--navy);color:#fff;font-size:14px;font-weight:600}
.topbar span{position:absolute;top:12px;display:flex;align-items:center;gap:8px}

/* nav */
.nav{left:80px;top:66px;width:1038px;height:78px;background:#fff;border-radius:4px;box-shadow:0 6px 22px rgba(20,36,74,.08)}
.brand{position:absolute;display:flex;align-items:center;gap:10px}
.brand-mark{width:40px;height:40px;background:var(--navy);border-radius:4px}
.brand-name{font-weight:700;font-size:32px;color:var(--navy);line-height:1}
.brand-tag{font-size:7.5px;font-weight:600;color:var(--navy);letter-spacing:.6px;margin-top:4px}
.menu a{position:absolute;top:33px;font-size:14.5px;font-weight:500;color:var(--ink);text-decoration:none}
.menu a.active{color:var(--blue);font-weight:600}
.menu .underline{position:absolute;left:369px;top:74px;width:56px;height:3px;background:var(--blue)}

/* hero */
.hero-sub{top:212px;font-size:24px;font-weight:500;color:var(--ink)}
.hero-title{top:234px;font-size:60px;font-weight:800;color:var(--navy);letter-spacing:.5px}
.hero-title .soft{color:#4a5675}

/* dashboard */
.dash{left:207px;top:383px;width:788px;height:479px;background:#fff;border-radius:10px;overflow:hidden;box-shadow:0 18px 50px rgba(20,36,74,.18)}
.dash-side{left:0;top:0;width:151px;height:479px;background:var(--dark-ui);color:#c9cfdc;font-size:8px}
.dash-side .item{position:absolute;left:18px;display:flex;align-items:center;gap:8px}
.dash-side .dot{width:8px;height:8px;border:1.5px solid #8790a5;border-radius:2px}
.dash-side .on{left:10px;width:130px;height:20px;background:#232a3c;border-radius:3px;padding-left:8px;color:#fff;font-weight:600}
.dash-side .on .dot{border-color:#4c86ff;background:#4c86ff}
.dash-main{left:151px;top:0;width:637px;height:479px;font-size:8px;color:var(--ink)}
.card-ui{position:absolute;border:1px solid var(--line);border-radius:5px;background:#fff}
.tiny{font-size:7px;color:var(--muted)}
.stat-num{font-size:17px;font-weight:700;color:var(--navy)}
.pill{display:inline-block;padding:1px 6px;border-radius:8px;font-size:6.5px;font-weight:600}
.pill.g{background:#e3f5eb;color:var(--green)}
.pill.b{background:#e4edff;color:var(--blue)}
.pill.a{background:#fdf1da;color:var(--amber)}
.pill.x{background:#eef0f4;color:var(--muted)}
.tbl-row{position:absolute;left:8px;width:346px;display:flex;font-size:7.5px;align-items:center}
.tbl-row span:nth-child(1){width:116px}
.tbl-row span:nth-child(2){width:70px}
.tbl-row span:nth-child(3){width:68px}
.bar-track{position:absolute;height:3px;background:#e3e8f1;border-radius:2px}
.bar-fill{position:absolute;height:3px;background:var(--blue);border-radius:2px}

/* trusted */
.trusted{top:938px;font-size:17px;font-weight:600;letter-spacing:1.2px}
.avatar{position:absolute;width:44px;height:44px;border-radius:50%;border:3px solid #fff;background:linear-gradient(160deg,#a7b3c9,#5d6a86)}
.client-logo{position:absolute;top:1066px;font-size:36px;color:#111;font-weight:500;transform:translateX(-50%);letter-spacing:1px}

/* product overview */
.po-frame{left:97px;top:1160px;width:343px;height:322px;border:2px solid var(--blue);border-radius:10px}
.po-card{left:111px;top:1172px;width:978px;height:437px;background:linear-gradient(160deg,#eef3fb,#e3ebf8);border:1px solid #c9d7ef;border-radius:10px}
.eyebrow{font-size:19px;font-weight:500;color:var(--ink)}
.po-title{font-size:33px;font-weight:700;color:#24438f;line-height:38px}
.po-text{font-size:14.5px;line-height:23px;color:#2c3344}
.po-shot{left:615px;top:1240px;width:442px;height:302px;border-radius:6px;background:linear-gradient(150deg,#1c2234,#252d44 60%,#1a2032)}
.dots{position:absolute;background-image:radial-gradient(circle,#14244a 2px,transparent 2.3px);background-size:14px 14px}

/* features */
.sec-title{font-size:40px;font-weight:700;color:var(--navy)}
.sec-title .soft{color:#3a4564}
.sec-rule{position:absolute;left:570px;width:60px;height:3px;background:var(--navy)}
.sec-lead{font-size:14.5px;line-height:26px;color:#2c3344}
.feat{position:absolute;top:1856px;width:219px;height:229px;background:#fff;border:1px solid var(--line);border-radius:4px;text-align:center;box-shadow:0 4px 18px rgba(20,36,74,.05)}
.feat .icon{position:absolute;left:74px;top:-36px;width:71px;height:71px;border-radius:50%;background:var(--navy);display:flex;align-items:center;justify-content:center}
.feat.hl .icon{background:var(--blue-2)}
.feat h3{position:absolute;top:55px;left:10px;right:10px;font-size:17px;font-weight:600;line-height:26px;color:var(--ink)}
.feat p{position:absolute;top:113px;left:16px;right:16px;font-size:13px;line-height:19px;color:var(--muted)}

/* pricing */
.price-table{left:114px;top:2287px;width:972px;height:258px;background:#fff;border:1px solid var(--line);border-radius:4px;overflow:hidden}
.pt-head{position:absolute;left:0;top:0;width:972px;height:54px;background:linear-gradient(90deg,#1a4fb8,#1f5dd0);color:#fff;font-size:20px;font-weight:600}
.pt-row{position:absolute;left:0;width:972px;font-size:16px;color:var(--ink)}
.pt-head span,.pt-row span{position:absolute}

/* benefits */
.ben-wrap{left:0;top:2712px;width:1200px;height:600px;background:#fff;border-radius:220px 220px 0 0}
.ben-circle{left:438px;top:2884px;width:324px;height:324px;border-radius:50%;background:radial-gradient(circle,#fff 55%,#eef3fb 100%);box-shadow:0 10px 40px rgba(20,36,74,.08);display:flex;align-items:center;justify-content:center;font-size:32px;font-weight:700;color:var(--navy)}
.ben-icon{position:absolute;width:78px;height:78px;border-radius:50%;background:#fff;border:2px solid var(--navy);display:flex;align-items:center;justify-content:center;box-shadow:0 0 0 6px #fff}
.ben-item h4{font-size:20px;font-weight:600;color:var(--ink)}
.ben-item p{font-size:17.5px;line-height:26px;color:#2c3344;font-weight:500}
.ben-item{position:absolute;width:300px}
.ben-item.l{text-align:right}

/* CTA */
.cta{left:111px;top:3296px;width:978px;height:276px;border-radius:10px;background:linear-gradient(160deg,#1d5ad0,#1848ad);box-shadow:0 16px 40px rgba(26,86,198,.25)}
.cta h2{position:absolute;top:62px;left:0;width:978px;text-align:center;font-size:41px;font-weight:700;color:#fff}
.cta .rule{position:absolute;left:459px;top:115px;width:60px;height:3px;background:#fff}
.cta p{position:absolute;top:130px;left:0;width:978px;text-align:center;font-size:14.5px;font-weight:500;color:#e6eeff}

/* footer */
.f-div{position:absolute;top:3679px;width:3px;height:192px;background:var(--navy)}
.f-title{font-size:15px;font-weight:700;color:var(--ink)}
.f-links{font-size:14px;line-height:22px;color:var(--ink);list-style:none}
.f-contact{font-size:14.5px;line-height:26px;color:var(--ink);font-weight:500}
.f-bottom{left:114px;top:3881px;width:976px;height:1px;background:#c9d1de}
.f-copy{font-size:13.5px;color:var(--ink)}
.social{position:absolute;top:3901px;width:28px;height:28px;border-radius:50%;background:var(--blue)}
</style>
</head>
<body>
<div class="page">

  <div class="abs hero-bg"></div>
  <svg class="abs" style="left:0;top:700px" width="1200" height="210" viewBox="0 0 1200 210" aria-hidden="true">
    <path d="M0 210 L0 200 C0 110 60 40 180 40 L1020 40 C1140 40 1200 110 1200 200 L1200 210 Z" fill="#e3ecf9"/>
    <path d="M0 210 L0 190 C20 60 80 20 200 20 L210 20 L210 210 Z" fill="#fff"/>
    <path d="M1200 210 L1200 190 C1180 60 1120 20 1000 20 L990 20 L990 210 Z" fill="#fff"/>
  </svg>
  <div class="abs band-bg"></div>
  <div class="abs foot-bg"></div>

  <!-- Top bar -->
  <header class="abs topbar">
    <span style="left:112px">
      <svg width="13" height="13" viewBox="0 0 24 24" fill="#fff"><path d="M6.6 10.8a15 15 0 0 0 6.6 6.6l2.2-2.2a1 1 0 0 1 1-.25 11.4 11.4 0 0 0 3.6.57 1 1 0 0 1 1 1V20a1 1 0 0 1-1 1A17 17 0 0 1 3 4a1 1 0 0 1 1-1h3.5a1 1 0 0 1 1 1c0 1.25.2 2.45.57 3.6a1 1 0 0 1-.25 1Z"/></svg>
      Call Us Now: <span style="position:static;font-weight:400">+1 555 010 2040</span>
    </span>
    <span style="left:802px">
      <svg width="12" height="13" viewBox="0 0 24 24" fill="#fff"><circle cx="12" cy="7" r="5"/><path d="M2 23c0-6 4.5-9 10-9s10 3 10 9Z"/></svg>Log In</span>
    <span style="left:917px">
      <svg width="16" height="14" viewBox="0 0 24 24" fill="none" stroke="#fff" stroke-width="2.2"><path d="M4 13v-2a8 8 0 0 1 16 0v2"/><rect x="2" y="13" width="5" height="7" rx="1" fill="#fff"/><rect x="17" y="13" width="5" height="7" rx="1" fill="#fff"/></svg>Customer Support</span>
  </header>

  <!-- Nav -->
  <nav class="abs nav">
    <div class="brand" style="left:31px;top:17px">
      <div class="brand-mark"></div>
      <div>
        <div class="brand-name">Merivantalo</div>
        <div class="brand-tag">PROFESSIONAL FOOTBALL SCOUTING REPORTS</div>
      </div>
    </div>
    <div class="menu">
      <a class="active" style="left:372px">Home</a>
      <a style="left:439px">Product</a>
      <a style="left:519px">Packages</a>
      <a style="left:609px">Packages</a>
      <a style="left:700px">FAQ</a>
      <a style="left:750px">Contact</a>
      <div class="underline"></div>
    </div>
    <div class="btn" style="left:830px;top:20px;width:177px;height:39px">Request a Demo <span class="chev"><svg width="10" height="10" viewBox="0 0 10 10"><path d="M3 1l4 4-4 4" stroke="#1a56c6" stroke-width="1.6" fill="none"/></svg></span></div>
  </nav>

  <!-- Hero -->
  <p class="center-text hero-sub">The Leading Platform for Professional</p>
  <h1 class="center-text hero-title">Football Scouting <span class="soft">Reports</span></h1>
  <div class="btn" style="left:495px;top:311px;width:210px;height:40px">Download Software <span class="chev"><svg width="10" height="10" viewBox="0 0 10 10"><path d="M3 1l4 4-4 4" stroke="#1a56c6" stroke-width="1.6" fill="none"/></svg></span></div>

  <!-- Dashboard preview -->
  <section class="abs dash" aria-label="Application dashboard preview">
    <aside class="abs dash-side">
      <div style="position:absolute;left:16px;top:14px;display:flex;align-items:center;gap:6px"><span style="width:14px;height:14px;background:#fff;border-radius:2px;display:inline-block"></span><span style="font-size:13px;font-weight:600;color:#fff">Merivantalo</span></div>
      <div class="item on" style="top:52px">
        <span class="dot"></span>Dashboard</div>
      <div class="item" style="top:82px"><span class="dot"></span>Players</div>
      <div class="item" style="top:108px"><span class="dot"></span>Scouting Reports</div>
      <div class="item" style="top:134px"><span class="dot"></span>Matches</div>
      <div class="item" style="top:160px"><span class="dot"></span>Analysis</div>
      <div class="item" style="top:186px"><span class="dot"></span>Templates</div>
      <div class="item" style="top:212px"><span class="dot"></span>Settings</div>
      <div style="position:absolute;left:18px;top:398px;display:flex;gap:8px;align-items:center">
        <span role="img" aria-label="User avatar" style="width:22px;height:22px;border-radius:50%;background:#7c879d;display:inline-block"></span>
        <span><b style="color:#fff;font-size:8px">Aaron Pell</b><br><span style="font-size:6.5px;color:#8a93a8">Chief Scout</span></span>
      </div>
      <div style="position:absolute;left:18px;top:436px;width:116px;font-size:7px;display:flex;justify-content:space-between"><span>Storage</span><span>78% Used</span></div>
      <div style="position:absolute;left:18px;top:450px;width:116px;height:3px;background:#343b4f;border-radius:2px"><div style="width:78%;height:3px;background:#fff;border-radius:2px"></div></div>
    </aside>

    <div class="abs dash-main">
      <div style="position:absolute;left:18px;top:14px;width:205px;height:20px;border:1px solid var(--line);border-radius:4px;padding:5px 0 0 22px" class="tiny">Search players, reports, matches...</div>
      <div style="position:absolute;left:420px;top:16px;width:16px;height:16px;border-radius:50%;border:1px solid var(--line)"></div>
      <div style="position:absolute;left:442px;top:16px;width:16px;height:16px;border-radius:50%;border:1px solid var(--line)"></div>
      <div style="position:absolute;left:467px;top:14px;width:88px;height:20px;background:var(--blue);border-radius:3px;color:#fff;font-size:7px;font-weight:600;padding:6px 0 0 9px">Generate Report ▾</div>
      <div style="position:absolute;left:562px;top:14px;width:20px;height:20px;background:var(--navy);border-radius:3px"></div>
      <div style="position:absolute;left:586px;top:14px;font-size:6.5px;font-weight:600;line-height:8px">Football<br><span class="tiny">Club</span></div>

      <div style="position:absolute;left:18px;top:50px;font-size:15px;font-weight:700">Dashboard</div>
      <div style="position:absolute;left:18px;top:72px" class="tiny">Welcome back, <b style="color:var(--ink)">Aaron</b>. Here's your scouting overview.</div>

      <div class="card-ui" style="left:18px;top:102px;width:128px;height:48px;padding:7px 9px"><div class="tiny">Players in Database</div><div style="display:flex;align-items:baseline;gap:10px;margin-top:6px"><span class="stat-num">243</span><span class="tiny" style="color:var(--green)">↗ +12 this week</span></div></div>
      <div class="card-ui" style="left:158px;top:102px;width:128px;height:48px;padding:7px 9px"><div class="tiny">Reports Generated</div><div style="display:flex;align-items:baseline;gap:10px;margin-top:6px"><span class="stat-num">187</span><span class="tiny" style="color:var(--green)">↗ +35 this month</span></div></div>
      <div class="card-ui" style="left:298px;top:102px;width:128px;height:48px;padding:7px 9px"><div class="tiny">Scouts Active</div><div style="display:flex;align-items:baseline;justify-content:space-between;margin-top:6px"><span class="stat-num">8</span><span class="tiny" style="color:var(--green)">● Online</span></div></div>
      <div class="card-ui" style="left:438px;top:102px;width:128px;height:48px;padding:7px 9px"><div class="tiny">Pending Reports</div><div style="display:flex;align-items:baseline;gap:10px;margin-top:6px"><span class="stat-num">12</span><span class="pill a">● Needs Review</span></div></div>

      <div class="card-ui" style="left:18px;top:161px;width:365px;height:158px">
        <div style="position:absolute;left:8px;top:8px;font-weight:700;font-size:8px">Recent Scouting Reports</div>
        <div style="position:absolute;right:10px;top:8px;font-size:7px;color:var(--blue);font-weight:600">View All →</div>
        <div class="tbl-row tiny" style="top:28px;font-size:6px;font-weight:600"><span>PLAYER</span><span>CLUB</span><span>POSITION</span><span>STATUS</span></div>
        <div class="tbl-row" style="top:42px"><span><b>T. Halvorsen</b> <span class="tiny">Midfielder</span></span><span>● NRD</span><span>CM</span><span class="pill g">● Completed</span></div>
        <div class="tbl-row" style="top:65px"><span><b>D. Okafor</b> <span class="tiny">Defender</span></span><span>● VLT</span><span>CB</span><span class="pill g">● Completed</span></div>
        <div class="tbl-row" style="top:88px"><span><b>P. Lindqvist</b> <span class="tiny">Forward</span></span><span>● KST</span><span>RW</span><span class="pill b">● In Progress</span></div>
        <div class="tbl-row" style="top:111px"><span><b>S. Marek</b> <span class="tiny">Midfielder</span></span><span>● BRM</span><span>DM</span><span class="pill a">● Pending</span></div>
        <div class="tbl-row" style="top:134px"><span><b>E. Navarro</b> <span class="tiny">Forward</span></span><span>● HLC</span><span>LW</span><span class="pill x">● Draft</span></div>
      </div>

      <div class="card-ui" style="left:393px;top:161px;width:183px;height:224px">
        <div style="position:absolute;left:9px;top:8px;font-weight:700">Player Overview</div>
        <div role="img" aria-label="Player portrait" style="position:absolute;left:9px;top:26px;width:26px;height:26px;border-radius:50%;background:#9aa5ba"></div>
        <div style="position:absolute;left:40px;top:28px;font-weight:700;color:var(--blue)">T. Halvorsen</div>
        <div style="position:absolute;left:40px;top:40px;font-size:5.5px;color:var(--muted)">Northgate FC · Midfielder</div>
        <div style="position:absolute;left:138px;top:24px;width:34px;height:34px;border-radius:50%;border:3px solid var(--green);text-align:center;font-weight:700;font-size:9px;padding-top:9px">82</div>
        <div style="position:absolute;left:9px;top:66px;font-weight:700;font-size:7px">Performance Scores</div>
        <div style="position:absolute;left:9px;top:80px;font-size:7px;line-height:18px">Technical<br>Tactical<br>Physical<br>Mental</div>
        <div style="position:absolute;left:150px;top:80px;font-size:7px;line-height:18px;font-weight:700">85<br>78<br>82<br>79</div>
        <div class="bar-track" style="left:48px;top:87px;width:92px"></div><div class="bar-fill" style="left:48px;top:87px;width:78px"></div>
        <div class="bar-track" style="left:48px;top:105px;width:92px"></div><div class="bar-fill" style="left:48px;top:105px;width:70px"></div>
        <div class="bar-track" style="left:48px;top:123px;width:92px"></div><div class="bar-fill" style="left:48px;top:123px;width:75px"></div>
        <div class="bar-track" style="left:48px;top:141px;width:92px"></div><div class="bar-fill" style="left:48px;top:141px;width:72px"></div>
        <div style="position:absolute;left:9px;top:160px;font-weight:700;font-size:7px">Last Match</div>
        <div style="position:absolute;left:9px;top:175px;font-size:7px"><b>NRD</b> vs <b>ORN</b> &nbsp;&nbsp;&nbsp;&nbsp; <b>2:1</b> &nbsp;&nbsp; <span class="tiny">Apr 21, 2024</span></div>
        <div style="position:absolute;right:10px;top:192px;font-size:6.5px;color:var(--blue);font-weight:600">View Report →</div>
      </div>

      <div class="card-ui" style="left:18px;top:330px;width:208px;height:132px">
        <div style="position:absolute;left:8px;top:7px;font-weight:700">Scouting Activity <span class="tiny">(Monthly)</span></div>
        <svg style="position:absolute;left:6px;top:24px" width="196" height="104" viewBox="0 0 196 104">
          <g font-size="6" fill="#6b7385" font-family="Montserrat,sans-serif">
            <text x="0" y="8">40</text><text x="0" y="28">30</text><text x="0" y="48">20</text><text x="0" y="68">10</text><text x="0" y="88">0</text>
            <text x="22" y="101">Nov</text><text x="50" y="101">Dec</text><text x="78" y="101">Jan</text><text x="106" y="101">Feb</text><text x="134" y="101">Mar</text><text x="162" y="101">Apr</text>
          </g>
          <g fill="#14244a"><rect x="26" y="40" width="8" height="46"/><rect x="54" y="55" width="8" height="31"/><rect x="82" y="35" width="8" height="51"/><rect x="110" y="50" width="8" height="36"/><rect x="138" y="28" width="8" height="58"/><rect x="166" y="12" width="8" height="74"/></g>
          <polyline points="30,45 58,55 86,38 114,56 142,30 170,12" fill="none" stroke="#1a56c6" stroke-width="1.2"/>
        </svg>
      </div>

      <div class="card-ui" style="left:233px;top:330px;width:150px;height:132px">
        <div style="position:absolute;left:8px;top:7px;font-weight:700">Report Generation</div>
        <svg style="position:absolute;left:6px;top:30px" width="50" height="50" viewBox="0 0 50 50"><circle cx="25" cy="25" r="20" stroke="#e3e8f1" stroke-width="6" fill="none"/><circle cx="25" cy="25" r="20" stroke="#1a56c6" stroke-width="6" fill="none" stroke-dasharray="95 126" transform="rotate(-90 25 25)"/><text x="25" y="28" text-anchor="middle" font-size="10" font-weight="700" fill="#14244a" font-family="Montserrat,sans-serif">76%</text></svg>
        <div style="position:absolute;left:64px;top:24px" class="tiny">Reports This Month</div>
        <div style="position:absolute;left:64px;top:42px;width:80px;font-size:7px;line-height:22px"><span class="tiny">Completed</span><span style="float:right;font-weight:700">35</span><br><span class="tiny">● Draft</span><span style="float:right;font-weight:700">12</span><br><span class="tiny">● Finalized</span><span style="float:right;font-weight:700">23</span></div>
      </div>

      <div class="card-ui" style="left:393px;top:388px;width:183px;height:74px">
        <div style="position:absolute;left:9px;top:7px;font-weight:700">Quick Actions</div>
        <div style="position:absolute;left:9px;top:24px;width:76px;height:18px;background:var(--blue);border-radius:3px;color:#fff;font-size:6.5px;font-weight:600;padding:5px 0 0 8px">+ New Report</div>
        <div style="position:absolute;left:90px;top:24px;width:76px;height:18px;border:1px solid var(--line);border-radius:3px;font-size:6.5px;padding:5px 0 0 8px">Add Player</div>
        <div style="position:absolute;left:9px;top:48px;width:76px;height:18px;border:1px solid var(--line);border-radius:3px;font-size:6.5px;padding:5px 0 0 8px">Upload Match</div>
        <div style="position:absolute;left:90px;top:48px;width:76px;height:18px;border:1px solid var(--line);border-radius:3px;font-size:6.5px;padding:5px 0 0 8px">Report Templates</div>
      </div>
    </div>
  </section>

  <!-- Trusted -->
  <p class="center-text trusted">TRUSTED BY LEADING PLAYERS</p>
  <div role="img" aria-label="Customer portrait" class="avatar" style="left:421px;top:976px"></div>
  <div role="img" aria-label="Customer portrait" class="avatar" style="left:461px;top:976px"></div>
  <div role="img" aria-label="Customer portrait" class="avatar" style="left:501px;top:976px"></div>
  <div role="img" aria-label="Customer portrait" class="avatar" style="left:537px;top:976px"></div>
  <div class="abs" style="left:573px;top:976px;width:44px;height:44px;border-radius:50%;border:3px solid #fff;background:var(--blue);color:#fff;font-weight:700;font-size:14px;text-align:center;line-height:38px">4.7</div>
  <div class="abs" style="left:623px;top:978px;font-size:19px;color:#f2b01e;letter-spacing:1px">★★★★★ <span style="color:var(--navy);font-size:16px;font-weight:600;letter-spacing:0">5 Star</span></div>
  <div class="abs" style="left:623px;top:1004px;font-size:11px;color:var(--muted)">From 150+ Reviews</div>

  <div class="client-logo" style="left:200px;font-weight:600">kelvora</div>
  <div class="client-logo" style="left:410px">dunmere</div>
  <div class="client-logo" style="left:601px;font-weight:600">tessaly</div>
  <div class="client-logo" style="left:819px;font-weight:400;letter-spacing:10px">OSTRAL</div>
  <div class="client-logo" style="left:1024px;font-weight:500;letter-spacing:4px">vinto</div>

  <!-- Product overview -->
  <div class="abs po-frame"></div>
  <section class="abs po-card">
    <p class="abs eyebrow" style="left:29px;top:50px">Product Overview</p>
    <h2 class="abs po-title" style="left:29px;top:78px;width:470px">Designed for Professional Football Scouting</h2>
    <p class="abs po-text" style="left:31px;top:180px;width:440px">Merivantalo provides a structured environment for creating professional scouting reports used in recruitment decisions, player representation, and performance analysis.</p>
    <p class="abs po-text" style="left:31px;top:272px;width:430px">Built for organizations that require consistent reporting standards and professional documentation.</p>
    <div class="btn" style="left:32px;top:343px;width:211px;height:40px">Download Software <span class="chev"><svg width="10" height="10" viewBox="0 0 10 10"><path d="M3 1l4 4-4 4" stroke="#1a56c6" stroke-width="1.6" fill="none"/></svg></span></div>
  </section>
  <div role="img" aria-label="Screenshot of the player profile screen in dark mode, with attribute bars, a heat map and a radar chart" class="abs po-shot"></div>
  <div class="dots" style="left:1090px;top:1530px;width:28px;height:100px"></div>
  <div class="dots" style="left:896px;top:1608px;width:222px;height:28px"></div>

  <!-- Core features -->
  <h2 class="center-text sec-title" style="top:1672px">Core <span class="soft">Features</span></h2>
  <div class="sec-rule" style="top:1730px"></div>
  <p class="center-text sec-lead" style="top:1746px;left:160px;width:880px">Merivantalo provides a structured environment for creating professional scouting reports used in recruitment decisions, player representation, and performance analysis.</p>

  <div class="abs" style="left:88px;top:1959px;width:210px;height:147px;border:2px solid var(--blue);border-radius:6px"></div>
  <div class="abs" style="left:1090px;top:1894px;width:16px;height:158px;border:2px solid var(--blue);border-left:none;border-radius:0 6px 6px 0"></div>

  <article class="feat" style="left:111px">
    <div class="icon"><svg width="34" height="34" viewBox="0 0 24 24" fill="none" stroke="#fff" stroke-width="1.4"><rect x="4" y="3" width="16" height="18" rx="1.5"/><path d="M7 15l3-3 3 2 4-5"/><path d="M7 7h6"/></svg></div>
    <h3>Structured Report Builder</h3>
    <p>Create scouting reports using a structured evaluation framework that ensures consistency across all reports.</p>
  </article>
  <article class="feat hl" style="left:364px">
    <div class="icon"><svg width="34" height="34" viewBox="0 0 24 24" fill="none" stroke="#fff" stroke-width="1.4"><rect x="4" y="3" width="14" height="18" rx="1.5"/><path d="M7 8h8M7 12h8M7 16h5"/><path d="M16 16l4-6"/></svg></div>
    <h3>Player Evaluation System</h3>
    <p>Create scouting reports using a structured evaluation framework that ensures consistency across all reports.</p>
  </article>
  <article class="feat" style="left:617px">
    <div class="icon"><svg width="34" height="34" viewBox="0 0 24 24" fill="none" stroke="#fff" stroke-width="1.4"><rect x="5" y="3" width="14" height="18" rx="1.5"/><path d="M9 3v2h6V3"/><path d="M8 10h8M8 14h8M8 18h5"/></svg></div>
    <h3>Executive-Level PDF Reports</h3>
    <p>Create scouting reports using a structured evaluation framework that ensures consistency across all reports.</p>
  </article>
  <article class="feat" style="left:870px">
    <div class="icon"><svg width="34" height="34" viewBox="0 0 24 24" fill="none" stroke="#fff" stroke-width="1.4"><circle cx="11" cy="11" r="8"/><path d="M3 11h16M11 3c3 3 3 13 0 16M11 3c-3 3-3 13 0 16"/><rect x="15" y="15" width="6" height="5" rx="1" fill="#14244a"/></svg></div>
    <h3>Offline &amp; Secure</h3>
    <p>Create scouting reports using a structured evaluation framework that ensures consistency across all reports.</p>
  </article>

  <!-- Pricing -->
  <h2 class="center-text sec-title" style="top:2192px">Pricing <span class="soft">Overview</span></h2>
  <div class="sec-rule" style="top:2250px"></div>
  <div class="dots" style="left:996px;top:2255px;width:122px;height:120px;clip-path:polygon(0 0,100% 0,100% 100%,80% 100%,80% 25%,0 25%)"></div>
  <div class="dots" style="left:78px;top:2462px;width:120px;height:120px;clip-path:polygon(0 0,20% 0,20% 75%,100% 75%,100% 100%,0 100%)"></div>
  <section class="abs price-table">
    <div class="pt-head"><span style="left:100px;top:14px">Package</span><span style="left:298px;top:14px">Target</span><span style="left:628px;top:14px">License</span></div>
    <div class="pt-row" style="top:54px;height:59px"><span style="left:100px;top:20px">Club</span><span style="left:298px;top:20px">Professional clubs</span><span style="left:628px;top:20px">Full scouting workflow</span></div>
    <div class="pt-row" style="top:113px;height:68px;background:#efefef"><span style="left:100px;top:24px">Agency</span><span style="left:298px;top:24px">Player representation firms</span><span style="left:628px;top:24px">Client scouting reports</span></div>
    <div class="pt-row" style="top:181px;height:77px"><span style="left:100px;top:28px">Player</span><span style="left:298px;top:28px">Individual athletes</span><span style="left:628px;top:28px">Personal performance reports</span></div>
  </section>
  <div class="btn" style="left:511px;top:2577px;width:178px;height:40px">View Packages <span class="chev"><svg width="10" height="10" viewBox="0 0 10 10"><path d="M3 1l4 4-4 4" stroke="#1a56c6" stroke-width="1.6" fill="none"/></svg></span></div>

  <!-- Benefits -->
  <div class="abs ben-wrap"></div>
  <h2 class="center-text sec-title" style="top:2786px">Our <span class="soft">Benefits</span></h2>
  <div class="sec-rule" style="top:2844px"></div>
  <div class="abs ben-circle">Merivantalo</div>

  <div class="ben-icon" style="left:391px;top:2910px"><svg width="34" height="34" viewBox="0 0 24 24" fill="none" stroke="#14244a" stroke-width="1.2"><rect x="5" y="3" width="14" height="18" rx="1"/><path d="M8 7h8M8 10h8"/><circle cx="12" cy="15" r="3"/></svg></div>
  <div class="ben-icon" style="left:391px;top:3064px"><svg width="34" height="34" viewBox="0 0 24 24" fill="none" stroke="#14244a" stroke-width="1.2"><path d="M6 3h9l4 4v14H6z"/><path d="M9 10h7M9 13h7M9 16h4"/><path d="M13 19l6-6"/></svg></div>
  <div class="ben-icon" style="left:711px;top:2910px"><svg width="34" height="34" viewBox="0 0 24 24" fill="none" stroke="#14244a" stroke-width="1.2"><circle cx="12" cy="9" r="6"/><path d="M12 6l1 2 2 .3-1.5 1.4.4 2.1L12 10.8l-1.9 1 .4-2.1L9 8.3l2-.3z"/><path d="M8 14l-2 7 3-1.5L11 21M16 14l2 7-3-1.5L13 21"/></svg></div>
  <div class="ben-icon" style="left:711px;top:3064px"><svg width="34" height="34" viewBox="0 0 24 24" fill="none" stroke="#14244a" stroke-width="1.2"><circle cx="12" cy="12" r="8"/><circle cx="12" cy="12" r="5.5"/><path d="M12 8v4l3 2"/></svg></div>

  <div class="ben-item l" style="left:72px;top:2916px"><h4>Save Scouting Time</h4><p>Generate reports in<br>minutes.</p></div>
  <div class="ben-item l" style="left:72px;top:3069px"><h4>Professional Reports</h4><p>Deliver executive-level<br>documents</p></div>
  <div class="ben-item" style="left:808px;top:2916px"><h4>Improve Decision Quality</h4><p>Structured analysis improves recruitment decisions.</p></div>
  <div class="ben-item" style="left:808px;top:3069px"><h4>Save Scouting Time</h4><p>Generate reports in<br>minutes.</p></div>

  <!-- CTA -->
  <section class="abs cta">
    <h2>Upgrade Your Scouting Reports</h2>
    <div class="rule"></div>
    <p>Join football professionals using structured scouting documentation.</p>
    <div class="btn dark" style="left:293px;top:167px;width:207px;height:38px">Download Software <span class="chev"><svg width="10" height="10" viewBox="0 0 10 10"><path d="M3 1l4 4-4 4" stroke="#14244a" stroke-width="1.6" fill="none"/></svg></span></div>
    <div class="btn light" style="left:514px;top:167px;width:172px;height:38px">View Packages <span class="chev"><svg width="10" height="10" viewBox="0 0 10 10"><path d="M3 1l4 4-4 4" stroke="#fff" stroke-width="1.6" fill="none"/></svg></span></div>
  </section>

  <!-- Footer -->
  <footer>
    <div class="brand" style="left:111px;top:3722px">
      <div class="brand-mark" style="width:44px;height:44px"></div>
      <div>
        <div class="brand-name" style="font-size:34px">Merivantalo</div>
        <div class="brand-tag" style="font-size:8.5px">PROFESSIONAL FOOTBALL SCOUTING REPORTS</div>
      </div>
    </div>
    <div class="f-div" style="left:451px"></div>
    <div class="f-div" style="left:740px"></div>

    <div class="abs" style="left:549px;top:3679px">
      <p class="f-title">QUICK LINKS</p>
      <ul class="f-links" style="margin-top:18px">
        <li>Home</li><li>About Us</li><li>Our Services</li><li>Projects</li><li>News</li><li>Contact Us</li>
      </ul>
    </div>

    <div class="abs" style="left:828px;top:3679px">
      <p class="f-title">CONTACT INFO</p>
    </div>
    <svg class="abs" style="left:829px;top:3720px" width="16" height="20" viewBox="0 0 24 30"><path d="M12 1C6 1 2 5.5 2 11c0 7 10 18 10 18s10-11 10-18C22 5.5 18 1 12 1Z" fill="#1a56c6"/><circle cx="12" cy="11" r="4" fill="#fff"/></svg>
    <p class="abs f-contact" style="left:859px;top:3716px">14 Harlow Lane, Eastbridge,<br>EB4 7QN</p>
    <svg class="abs" style="left:828px;top:3786px" width="19" height="14" viewBox="0 0 24 18"><rect x="1" y="1" width="22" height="16" rx="1" fill="#1a56c6"/><path d="M1 2l11 8 11-8" stroke="#fff" stroke-width="1.6" fill="none"/></svg>
    <p class="abs f-contact" style="left:859px;top:3780px">hello@merivantalo.com</p>
    <svg class="abs" style="left:829px;top:3826px" width="17" height="17" viewBox="0 0 24 24" fill="#1a56c6"><path d="M6.6 10.8a15 15 0 0 0 6.6 6.6l2.2-2.2a1 1 0 0 1 1-.25 11.4 11.4 0 0 0 3.6.57 1 1 0 0 1 1 1V20a1 1 0 0 1-1 1A17 17 0 0 1 3 4a1 1 0 0 1 1-1h3.5a1 1 0 0 1 1 1c0 1.25.2 2.45.57 3.6a1 1 0 0 1-.25 1Z"/></svg>
    <p class="abs f-contact" style="left:859px;top:3823px;text-decoration:underline;font-weight:600">+1 555 010 2040</p>

    <div class="abs f-bottom"></div>
    <p class="abs f-copy" style="left:114px;top:3907px">© 2026 Merivantalo. All Rights Reserved.</p>
    <span class="social" style="left:550px"></span>
    <span class="social" style="left:589px"></span>
    <span class="social" style="left:629px"></span>
    <p class="abs f-copy" style="left:868px;top:3907px">Privacy &nbsp;&nbsp;|&nbsp;&nbsp; Terms &nbsp;&nbsp;|&nbsp;&nbsp; Disclaimer</p>
  </footer>

</div>
</body>
</html>
```